accomplished personal trainer, former elite gymnast from Russia, highly professional and experienced

Established Fitness trainer in California requires a new web site to attract personal clients and build her group exercise classes.

Here is an example of another fitness trainer's site that I really liked the technology:
http://www.tedvorlam.com

Below I have inserted my current web site: www.quelbornfitnesslodi.com
You can use this web site for the principal content, such as my background and qualifications.

Target Market(s)

Anyone who wants to improve their fitness levels and wellness in general. Anyone who needs directions and instruction on how to exercise. I can train anyone from elite athlete to a disabled person.

Industry/Entity Type

Fitness

Coding

Coded - Design and coding required

Number of Pages Required

5+ page

Font styles to use
Sans Serif

Requirements
Must have
• Easy to navigate main info about me, location, services, contact, benefits of using my services.
• Would be great to create unique representation of me as a trainer and a person, using new technologies and new ideas. Make it different from the other websites. Having its own character. Not too complicated and heavy with information, but an eye catching, useful and fun to navigate.
Nice to have
• new technology, easy access to information, the idea of enjoyment of life, lightness about achieving any goal, spiritual wisdom, unique design. I am planning to insert educational videos, advise, maybe jokes. Sign in, shopping cart, logo, should be easy for me to make changes in content.
Should not have
• cliché, outdated technology, too complicated,

```html
<!DOCTYPE html>
<html lang="en">
<head>
<meta charset="utf-8">
<title>Quelborn Fitness Lodi</title>
<link href="https://fonts.googleapis.com/css2?family=Lato:ital,wght@0,300;0,400;0,700;1,400&display=swap" rel="stylesheet">
<style>
:root{
  --green:#4caf63;
  --green-dark:#3d9a53;
  --orange:#e08a1e;
  --navy:#2e3a4b;
  --ink:#333;
  --muted:#9a9a9a;
  --line:#e6e6e6;
  --footer:#f5f6f8;
}
*{box-sizing:border-box;margin:0;padding:0}
html,body{width:1200px;height:2985px;overflow:hidden;background:#fff;font-family:'Lato',sans-serif;color:var(--ink)}
.page{position:relative;width:1200px;height:2985px}
.abs{position:absolute}
.topbar{left:0;top:0;width:1200px;height:32px;background:var(--green);color:#fff;font-size:10px;display:flex;align-items:center}
.topbar .info{position:absolute;left:244px;display:flex;gap:34px;align-items:center}
.topbar .info span{display:flex;align-items:center;gap:6px}
.lang-box{display:inline-block;width:14px;height:12px;background:#fff;margin-left:4px}
.socials{position:absolute;left:782px;display:flex;gap:9px}
.dot{width:10px;height:10px;border-radius:50%;background:#fff}
.brand{left:0;top:50px;width:1200px;text-align:center;font-size:22px;font-weight:400;letter-spacing:.5px;color:#222}
.nav{left:0;top:96px;width:1200px;height:38px;border-top:1px solid var(--line)}
.nav ul{list-style:none;display:flex;position:absolute;left:232px;top:0;height:38px;align-items:center;font-size:10px;color:#444}
.nav li{padding:0 22px;border-left:1px solid var(--line);line-height:14px}
.nav li:first-child{border:none;padding-left:0;color:var(--green)}
.search{position:absolute;left:942px;top:9px;width:20px;height:20px;border-radius:50%;border:1px solid #ddd}
.hero{left:0;top:134px;width:1200px;height:458px;background:linear-gradient(180deg,#c9d6c4 0%,#9fba83 45%,#5f9a3e 100%)}
.hero h1{position:absolute;left:0;width:1200px;top:126px;text-align:center;color:#fff;font-size:46px;font-weight:700}
.hero p{position:absolute;left:400px;width:430px;top:186px;text-align:center;color:#fff;font-size:15px;font-weight:700;line-height:22px}
.btn{display:inline-block;font-size:9px;font-weight:700;text-transform:uppercase;padding:0 14px;line-height:30px;height:30px}
.btn-orange{background:var(--orange);color:#fff}
.btn-outline{border:1px solid #fff;color:#fff;line-height:28px}
.hero .actions{position:absolute;left:494px;top:268px;display:flex;gap:14px}
.hero .arrow{position:absolute;top:210px;width:36px;height:36px;display:flex;align-items:center;justify-content:center}
.pager{position:absolute;left:554px;top:404px;display:flex;gap:8px}
.pager i{width:18px;height:18px;border-radius:50%;border:1px solid #fff;font-style:normal;font-size:8px;color:#fff;display:flex;align-items:center;justify-content:center}
.pager i.on{background:#fff;color:#333}
.card{top:654px;width:232px;height:190px;border:1px solid #eee;text-align:center}
.card .icon{position:absolute;left:84px;top:-32px;width:64px;height:64px;border-radius:50%;background:var(--green);display:flex;align-items:center;justify-content:center}
.card .icon.dark{background:#222;border:4px solid var(--orange)}
.card h3{margin-top:48px;font-size:11px;font-weight:700}
.card p{margin:10px auto 0;width:160px;font-size:8px;line-height:13px;color:var(--muted)}
.card .btn{margin-top:16px;height:24px;line-height:22px;border:1px solid #ddd;color:#999;font-weight:400;padding:0 18px;text-transform:none}
.card .btn.btn-orange{border-color:var(--orange);color:#fff;font-weight:700}
.quote-band{left:0;top:884px;width:1200px;height:292px;background:linear-gradient(135deg,#6d6560 0%,#3a3838 40%,#7a7670 70%,#4a4a48 100%)}
.quote-strip{position:absolute;left:0;top:38px;width:1200px;height:104px;background:rgba(235,235,235,.88);text-align:center}
.quote-strip q{display:block;margin-top:30px;font-style:italic;font-size:15px;line-height:21px;color:#555;quotes:"\201C" "\201D"}
.quote-strip small{display:block;margin-top:6px;font-size:8px;color:#888}
.section-title{width:1200px;left:0;text-align:center;font-size:23px;font-weight:300;color:#444}
.section-sub{width:1200px;left:0;text-align:center;font-size:8px;color:var(--muted)}
.thumb{top:1292px;width:356px;height:198px}
.thumb .play{position:absolute;left:162px;top:83px;width:30px;height:30px;border-radius:50%;background:#fff}
.round{width:32px;height:32px;border-radius:50%;display:flex;align-items:center;justify-content:center}
.stats-band{left:0;top:1556px;width:1200px;height:372px;background:linear-gradient(180deg,#5c6e40 0%,#7f9461 40%,#6b8a3f 75%,#4e7830 100%)}
.stats-panel{position:absolute;left:236px;top:26px;width:734px;height:128px;background:rgba(30,30,30,.55);display:flex}
.stat{flex:1;text-align:center;color:#fff;padding-top:26px}
.stat b{display:block;font-size:48px;font-weight:300;line-height:50px}
.stat span{display:block;font-size:10px;padding-left:60px}
.feature-post{left:236px;top:2056px;width:356px;height:264px;display:flex}
.feature-post .text{width:188px;background:#2a2a2a;color:#fff;padding:16px 18px}
.feature-post h4{font-size:14px;font-weight:700}
.feature-post p{font-size:8.5px;line-height:13px;color:#ccc;margin-top:10px}
.feature-post .date{font-size:9px;font-weight:700;margin-top:8px}
.feature-post .sq{display:inline-block;width:16px;height:16px;margin-top:14px;margin-right:4px}
.feature-post .photo{flex:1;background:linear-gradient(160deg,#4a6a3a,#2f4d77 60%,#1f3147)}
.post{left:612px;width:358px;height:90px;border-bottom:1px solid var(--line)}
.post .date-box{position:absolute;left:0;top:0;width:62px;height:76px;background:var(--green);color:#fff;text-align:center}
.post .date-box b{display:block;font-size:28px;font-weight:300;margin-top:10px}
.post .date-box small{font-size:9px}
.post .mini{position:absolute;left:0;top:0;width:62px;height:76px;background:linear-gradient(180deg,#6c8f4e,#3b5a7a)}
.post .mini span{position:absolute;left:0;bottom:0;width:62px;height:20px;background:rgba(46,58,75,.9);color:#fff;font-size:9px;text-align:center;line-height:20px}
.post h5{position:absolute;left:74px;top:-2px;font-size:11px;font-weight:700;color:#222}
.post h5.hl{color:var(--green)}
.post p{position:absolute;left:74px;top:16px;width:282px;font-size:8px;line-height:12px;color:var(--muted)}
.post .meta{position:absolute;left:74px;top:66px;font-size:8.5px;color:var(--green)}
.news-band{left:0;top:2382px;width:1200px;height:316px;background:linear-gradient(180deg,#6b8e4a 0%,#a8b97a 35%,#c08a6a 65%,#3d5a7a 100%)}
.news-box{position:absolute;left:236px;top:194px;width:734px;height:88px;background:#fff;border-left:6px solid var(--orange)}
.news-box h4{position:absolute;left:20px;top:18px;font-size:15px;font-weight:400;color:#333}
.news-box p{position:absolute;left:20px;top:40px;width:300px;font-size:8px;line-height:12px;color:var(--muted)}
.news-box .field{position:absolute;left:362px;top:26px;width:222px;height:30px;background:#f0f0f0;font-size:9px;color:#888;padding:9px 12px}
.news-box .btn{position:absolute;left:590px;top:26px;width:110px;text-align:center;font-size:11px;text-transform:none}
.green-rule{left:0;top:2698px;width:1200px;height:6px;background:var(--green)}
.footer{left:0;top:2704px;width:1200px;height:281px;background:var(--footer)}
.col{top:64px;width:166px}
.col h6{font-size:10px;font-weight:700;letter-spacing:2px;color:#333;padding-bottom:10px;border-bottom:1px solid #ddd;width:80px}
.col ul{list-style:none;margin-top:26px}
.col li{font-size:9px;color:#333;margin-bottom:22px;line-height:12px}
.col li small{display:block;font-size:8px;color:var(--muted)}
.col .about-name{margin-top:26px;font-size:14px;color:#333}
.col .about-text{margin-top:20px;font-size:8px;line-height:13px;color:var(--muted)}
.col .more{margin-top:12px;font-size:8px;font-weight:700;color:#333}
.copyright{left:236px;top:258px;font-size:8px;color:var(--muted)}
.foot-social{left:800px;top:254px;display:flex;gap:9px}
.foot-social .dot{background:#8fa0b5}
</style>
</head>
<body>
<div class="page">

  <div class="abs topbar">
    <div class="info">
      <span><svg width="10" height="10" viewBox="0 0 10 10"><circle cx="5" cy="5" r="4" fill="none" stroke="#fff"/><path d="M1 5h8M5 1v8" stroke="#fff" stroke-width=".8"/></svg>Languages: <b>English</b><i class="lang-box"></i></span>
      <span><svg width="9" height="9" viewBox="0 0 10 10"><path d="M2 1l2 2-1 1.5c.8 1.4 1.6 2.2 3 3L7.5 6l2 2-1.5 1.6C4.5 9 1 5.5.5 2.5z" fill="#fff"/></svg>+1 (555) 014-2290</span>
      <span><svg width="11" height="8" viewBox="0 0 11 8"><rect x=".5" y=".5" width="10" height="7" fill="none" stroke="#fff"/><path d="M.5.5l5 4 5-4" fill="none" stroke="#fff"/></svg>hello@quelbornlodi.com</span>
    </div>
    <div class="socials"><i class="dot"></i><i class="dot"></i><i class="dot"></i><i class="dot"></i><i class="dot"></i><i class="dot"></i><i class="dot"></i><i class="dot"></i><i class="dot"></i></div>
  </div>

  <div class="abs brand">QUELBORN FITNESS LODI</div>

  <nav class="abs nav">
    <ul>
      <li>&#8962; HOME</li><li>GROUP CLASSES</li><li>PERSONAL TRAINING</li><li>ABOUT QUELBORN</li><li>CONTACT</li><li>BLOG</li>
    </ul>
    <span class="search"></span>
  </nav>

  <section class="abs hero" role="img" aria-label="Group of people doing squats outdoors on a sunny lawn">
    <h1>Fitness Outdoors</h1>
    <p>Nam ornare diam eu porta rutrum. In faucibus mi diam, et efficitur mauris semper a.</p>
    <div class="actions"><span class="btn btn-orange">Read More</span><span class="btn btn-outline">Online Booking</span></div>
    <span class="arrow" style="left:0;background:var(--orange)"><svg width="10" height="10"><path d="M7 1L3 5l4 4" stroke="#fff" stroke-width="1.5" fill="none"/></svg></span>
    <span class="arrow" style="left:1164px;background:#2a2a2a"><svg width="10" height="10"><path d="M3 1l4 4-4 4" stroke="#fff" stroke-width="1.5" fill="none"/></svg></span>
    <div class="pager"><i>1</i><i class="on">2</i><i>3</i><i>4</i></div>
  </section>

  <div class="abs card" style="left:236px">
    <div class="icon"><svg width="26" height="26" viewBox="0 0 26 26" fill="#fff"><circle cx="9" cy="7" r="3"/><circle cx="17" cy="7" r="3"/><circle cx="13" cy="12" r="3"/><rect x="6" y="15" width="14" height="7" rx="3"/></svg></div>
    <h3>Group Classes/ Boot Camps</h3>
    <p>Praesent turpis mauris, aliquet id dolor. Gravida adipiscing lectus at rutrum. Aenean at posuere risus.</p>
    <span class="btn">Read More</span>
  </div>
  <div class="abs card" style="left:486px">
    <div class="icon dark"><svg width="26" height="26" viewBox="0 0 26 26" fill="#fff"><circle cx="9" cy="6" r="3"/><rect x="4" y="11" width="18" height="3"/><rect x="6" y="14" width="3" height="8"/><rect x="17" y="14" width="3" height="8"/></svg></div>
    <h3>Personal Training</h3>
    <p>Praesent turpis mauris, aliquet id dolor. Gravida adipiscing lectus at rutrum. Aenean at posuere risus.</p>
    <span class="btn btn-orange">Read More</span>
  </div>
  <div class="abs card" style="left:736px">
    <div class="icon"><svg width="28" height="28" viewBox="0 0 28 28"><circle cx="14" cy="14" r="11" fill="none" stroke="#fff" stroke-width="2"/><circle cx="14" cy="9" r="1.6" fill="#fff"/><rect x="12.6" y="12" width="2.8" height="9" fill="#fff"/></svg></div>
    <h3>About Quelborn Fitness</h3>
    <p>Praesent turpis mauris, aliquet id dolor. Gravida adipiscing lectus at rutrum. Aenean at posuere risus.</p>
    <span class="btn">Read More</span>
  </div>

  <section class="abs quote-band" role="img" aria-label="Close-up of a woman training with a kettlebell">
    <div class="quote-strip">
      <q>The best thing about working out with Marina is the variety she offers in each workout.<br>I always leave feeling that I tried something new.</q>
      <small>– Happy Client</small>
    </div>
  </section>

  <h2 class="abs section-title" style="top:1206px">Educational Videos</h2>
  <div class="abs section-sub" style="top:1242px">Lorem ipsum dolor sit amet, consectetur</div>
  <div class="abs round" style="left:152px;top:1370px;background:var(--navy)"><svg width="10" height="10"><path d="M6.5 1.5L3 5l3.5 3.5" stroke="#fff" stroke-width="1.5" fill="none"/></svg></div>
  <div class="abs thumb" style="left:236px;background:linear-gradient(160deg,#5b7a3a,#8aa05a 50%,#4e6b30)" role="img" aria-label="Video still: woman doing a side lunge stretch in a park"><span class="play"></span></div>
  <div class="abs thumb" style="left:614px;background:linear-gradient(160deg,#4f7038,#9bb06a 50%,#5a7a3a)" role="img" aria-label="Video still: group stretching together outdoors"><span class="play"></span></div>
  <div class="abs round" style="left:1020px;top:1370px;background:var(--orange)"><svg width="10" height="10"><path d="M3.5 1.5L7 5 3.5 8.5" stroke="#fff" stroke-width="1.5" fill="none"/></svg></div>

  <section class="abs stats-band" role="img" aria-label="Woman stretching outdoors among trees">
    <div class="stats-panel">
      <div class="stat"><b>2.438</b><span>Customers</span></div>
      <div class="stat"><b>9.845</b><span>Works</span></div>
      <div class="stat"><b>9.845</b><span>Classes</span></div>
      <div class="stat"><b>1.276</b><span>Support Posts</span></div>
    </div>
  </section>

  <h2 class="abs section-title" style="top:1962px">Tips to Members</h2>
  <div class="abs section-sub" style="top:1996px">Donec suscipit, diam condimentum viverra ornare, turpis ipsum molestie quam</div>

  <article class="abs feature-post">
    <div class="text">
      <h4>Lacinia at sollicitudin</h4>
      <p>Vivamus viverra, ligula non tincidunt pulvinar, augue est sagittis leo, id feugiat enim lorem quis nisl. Quisque ac arcu egestas, convallis risus vitae, gravida enim.</p>
      <div class="date">27 Feb, 2016</div>
      <span class="sq" style="background:var(--orange)"></span><span class="sq" style="border:1px solid #888"></span>
    </div>
    <div class="photo" role="img" aria-label="Person stretching on a mat outdoors"></div>
  </article>

  <article class="abs post" style="top:2054px">
    <div class="date-box"><b>29</b><small>Nov</small></div>
    <h5 class="hl">Pellentesque lorem massa, lacinia at sollicitudin</h5>
    <p>Lorem ipsum dolor sit amet, consectetur adipiscing elit. Vivamus a aliquet orci. Ut interdum mauris eget, non aliquet felis interdum id</p>
    <div class="meta">27 comments &nbsp; / &nbsp; Blog Design &nbsp; / &nbsp; Read more</div>
  </article>
  <article class="abs post" style="top:2148px">
    <div class="mini" role="img" aria-label="Couple training outdoors"><span>29, Nov</span></div>
    <h5>Massa, lacinia at sollicitudin</h5>
    <p>Lorem ipsum dolor sit amet, consectetur adipiscing elit. Vivamus a aliquet orci. Ut interdum mauris eget, non aliquet felis interdum id</p>
    <div class="meta">27 comments &nbsp; / &nbsp; Blog Design &nbsp; / &nbsp; Read more</div>
  </article>
  <article class="abs post" style="top:2242px;border:none">
    <div class="mini" role="img" aria-label="Women exercising in a park"><span>29, Nov</span></div>
    <h5>Lorem massa, lacinia at sollicitudin</h5>
    <p>Lorem ipsum dolor sit amet, consectetur adipiscing elit. Vivamus a aliquet orci. Ut interdum mauris eget, non aliquet felis interdum id</p>
    <div class="meta">27 comments &nbsp; / &nbsp; Blog Design &nbsp; / &nbsp; Read more</div>
  </article>

  <section class="abs news-band" role="img" aria-label="Smiling group stretching arms together outdoors">
    <div class="news-box">
      <h4>Subscribe for Newsletter</h4>
      <p>Quisque lacinia tortor in mauris egestas, nec adipiscing nisi auctor. Suspendisse potenti. Nam in consequat turpis.</p>
      <div class="field">Enter email id</div>
      <span class="btn btn-orange">Subscribe</span>
    </div>
  </section>
  <div class="abs green-rule"></div>

  <footer class="abs footer">
    <div class="abs col" style="left:236px">
      <h6>RECENT POST</h6>
      <ul>
        <li>Amazing Standard Post<small>26 May, 2017</small></li>
        <li>Slideshow Images<small>26 May, 2017</small></li>
        <li>Video Post<small>26 May, 2017</small></li>
      </ul>
    </div>
    <div class="abs col" style="left:424px">
      <h6 style="width:140px">RECENT COMMENTS</h6>
      <ul>
        <li>Rosa Lint<small>Popular sit Lorem ipsum dolor sit amet</small></li>
        <li>Owen Pratel<small>Lorem ipsum dolor sit amet</small></li>
        <li>Lena Vortanova<small>Excitatory Lorem ipsum dolor sit amet</small></li>
      </ul>
    </div>
    <div class="abs col" style="left:612px">
      <h6>ARCHIVES</h6>
      <ul>
        <li>March 2017<small>1509 Posted</small></li>
        <li>June 2017<small>1509 Posted</small></li>
        <li>July 2017<small>1509 Posted</small></li>
      </ul>
    </div>
    <div class="abs col" style="left:800px">
      <h6>ABOUT US</h6>
      <div class="about-name">QUELBORN FITNESS LODI</div>
      <p class="about-text">We are constantly working to raise the bar on our services. If you have any questions or concerns about your experience, please let us know.</p>
      <div class="more">LEARN MORE</div>
    </div>
    <div class="abs copyright">© 2016 Quelborn Fitness. All Rights Reserved</div>
    <div class="abs foot-social"><i class="dot"></i><i class="dot"></i><i class="dot"></i><i class="dot"></i><i class="dot"></i><i class="dot"></i><i class="dot"></i><i class="dot"></i></div>
  </footer>

</div>
</body>
</html>
```